lantern pathway for children needs a website designer

We need a website designer for our new extension to our company known as 'lantern pathway' providing shadow support services to children based in Singapore. We are a sister branch of a private clinic 'Bright horizons' providing speech language, occupational, and educational therapy to children.

We would like to use our own photos. So the selected design should have a frame with pictures to give us an idea but we will replace them with our own. We will be needing help with inputting information and changing information throughout.

We would like to see designs that are simple, and professional. We have a logo (see attached). The result should convey professionalism in shadow support, fostering independent thinking and moving students towards self-learning.

Target Market(s)

Teachers, psychologists, parents

Industry/Entity Type

Clinic

Requirements
Should not have
• too distracting colours

```html
<!DOCTYPE html>
<html lang="en">
<head>
<meta charset="utf-8">
<title>Lantern Pathway</title>
<link href="https://fonts.googleapis.com/css2?family=Signika:wght@300;400&display=swap" rel="stylesheet">
<style>
:root{
  --red:#a30f0f;
  --red-dark:#860808;
  --band:#f0f0f0;
  --text:#676767;
  --header-bg:#ececec;
  --footer-bg:#393939;
}
*{margin:0;padding:0;box-sizing:border-box}
html,body{width:1060px;height:1200px;overflow:hidden}
body{position:relative;background:#fff;font-family:'Signika',sans-serif;font-weight:300;color:var(--text);font-size:12.4px;line-height:17.7px}
.abs{position:absolute}
.site-header{left:0;top:0;width:1060px;height:90px;background:var(--header-bg)}
.brand{left:115px;top:30px;display:flex;align-items:center;gap:8px;font-size:27px;font-weight:400;color:var(--red);line-height:30px}
.brand-mark{width:14px;height:14px;background:var(--red);border-radius:50%}
.nav{left:408px;top:51px;display:flex;font-size:12.4px;font-weight:300}
.nav a{color:#444;text-decoration:none;padding:0 10px;border-left:1px dotted #888;line-height:22px}
.nav a:first-child{border-left:none;color:var(--red)}
.hero-frame{left:112px;top:106px;width:836px;height:340px;border:1px solid #e2e2e2;box-shadow:0 1px 3px rgba(0,0,0,.12)}
.hero-photo{left:116px;top:110px;width:829px;height:333px;background:linear-gradient(90deg,#b59a86 0%,#c8a592 30%,#c7c5c8 58%,#d9dade 100%)}
.hero-title{right:143px;top:148px;text-align:right;color:var(--red);font-size:33px;line-height:41px;font-weight:400}
.hero-text{right:144px;top:250px;width:260px;text-align:right;font-size:12.4px;line-height:16px;color:#555}
.btn{display:flex;align-items:center;justify-content:center;background:linear-gradient(#b31414,var(--red-dark));color:#fff;font-size:12.4px;font-weight:300;border-radius:2px}
.dots{left:853px;top:410px;display:flex;gap:5px}
.dots span{width:11px;height:11px;border-radius:50%;background:#fff}
.dots span:first-child{background:#888}
.band{background:var(--band);color:var(--red);font-size:17.5px;font-weight:400;padding-left:15px;display:flex;align-items:center}
.photo{background:linear-gradient(135deg,#3e4442,#2c302f);border:3px solid #fff;outline:1px solid #ddd}
.arrow{display:inline-block;width:20px;color:#222;font-size:10px}
.q{color:var(--red);font-weight:300}
.register{left:681px;top:798px;width:261px;height:280px;background:#e8e8e8}
.register-head{height:37px;background:linear-gradient(#b31414,var(--red-dark));color:#fff;font-size:14.5px;font-weight:300;padding-left:16px;display:flex;align-items:center}
.field{background:#fff;border:1px solid #ddd;font-style:italic;color:#aaa;font-size:11px;padding:6px 13px}
.site-footer{left:0;top:1116px;width:1060px;height:84px;background:var(--footer-bg);color:#eee;font-size:12.4px;font-weight:300}
.social{width:28px;height:28px;border-radius:4px}
</style>
</head>
<body>
<header class="abs site-header">
  <div class="abs brand"><span class="brand-mark"></span>Lantern Pathway</div>
  <nav class="abs nav">
    <a>Home</a><a>About Us</a><a>Mission</a><a>Our Services</a><a>Shadow Support</a><a>For Referrers</a><a>Contact</a>
  </nav>
</header>

<div class="abs hero-frame"></div>
<div class="abs hero-photo" role="img" aria-label="Therapist and young girl reading a picture book together"></div>
<h1 class="abs hero-title">Speech Language<br>Therapy</h1>
<p class="abs hero-text">Lantern Pathway was borne out of our Speech language Pathologists’ frustration at a frequent lack of carry-over of goals to a classroom setting by external shadows.Carrying over of goals.</p>
<div class="abs btn" style="left:806px;top:344px;width:110px;height:29px">Read More &gt;&gt;</div>
<div class="abs dots"><span></span><span></span><span></span><span></span></div>

<h2 class="abs band" style="left:115px;top:482px;width:477px;height:36px">About Us</h2>
<div class="abs photo" style="left:115px;top:533px;width:194px;height:130px" role="img" aria-label="Two women at a chalkboard with drawn speech bubbles"></div>
<p class="abs" style="left:328px;top:533px;width:265px">Lantern Pathway is part of the Harbourview Therapy Group of Companies, who are providing speech language therapy, occupational therapy and educational therapy services . Lantern Pathway aims to work in an integrated manner, respecting the work of the respective. professionals involved and collaborating effectively.</p>
<p class="abs" style="left:117px;top:675px;width:470px">Lantern Pathway was borne out of our Speech language Pathologists’ frustration at a frequent lack of carry-over of goals to a classroom setting by external shadows.</p>
<div class="abs btn" style="left:117px;top:729px;width:92px;height:30px">Read More</div>

<h2 class="abs band" style="left:609px;top:482px;width:336px;height:36px">Our Services</h2>
<p class="abs" style="left:612px;top:534px;width:340px">We provide a full fledged, seamless service that serves to:</p>
<p class="abs" style="left:610px;top:566px;width:340px"><span class="arrow">&rarr;</span>Train shadows with a strong focus on equipping them with dynamic, clinical skills.</p>
<p class="abs" style="left:610px;top:628px;width:340px"><span class="arrow">&rarr;</span>Provide families with well-trained Shadows who are mentored by Speech Language Pathologists and Professional Therapists to carry out shadow support.</p>
<div class="abs btn" style="left:609px;top:705px;width:93px;height:30px">Read More</div>

<h2 class="abs band" style="left:115px;top:798px;width:265px;height:36px">Mission</h2>
<p class="abs" style="left:115px;top:851px;width:265px">Lantern Pathway was borne out of our Speech language Pathologists’ frustration at a frequently lack of carry-over of goals to a classroom setting by external shadows. Carrying over of goals in real settings is highly important as it allows for studen to generalize skills quicker.</p>
<p class="abs" style="left:115px;top:965px;width:265px">By generalizing skills, this means that the student would have truly learned a specific skill and can apply this in different settings.</p>
<div class="abs btn" style="left:117px;top:1040px;width:92px;height:30px">Read More</div>

<h2 class="abs band" style="left:397px;top:798px;width:265px;height:36px">Shadow Support</h2>
<p class="abs q" style="left:399px;top:851px">Q :&nbsp; What is shadow support?</p>
<p class="abs" style="left:399px;top:885px;width:265px">A shadow support is para-professional who can help a strugglig student to integrate and learn in their school environmenedaes.</p>
<p class="abs" style="left:399px;top:941px;width:265px">At different points in a student’s life, there may be a need for a para-professional who could step in to help make a difference.&nbsp; Students who need shadows are those.</p>
<div class="abs btn" style="left:399px;top:1034px;width:93px;height:30px">Read More</div>

<section class="abs register">
  <h2 class="register-head">Register as a Shadow</h2>
  <div class="abs field" style="left:17px;top:58px;width:227px;height:28px">Enter your Name..</div>
  <div class="abs field" style="left:17px;top:99px;width:227px;height:29px">Enter your Email...</div>
  <div class="abs field" style="left:17px;top:141px;width:227px;height:69px">Leave Message...</div>
  <div class="abs btn" style="left:21px;top:230px;width:92px;height:30px;font-size:13px">Submit</div>
</section>

<footer class="abs site-footer">
  <p class="abs" style="left:115px;top:31px">©2014 Lantern Pathway - Terms of Service - Privacy Policy</p>
  <div class="abs social" style="left:834px;top:29px;background:#3b5f9a"></div>
  <div class="abs social" style="left:874px;top:29px;background:#3fb3d4"></div>
  <div class="abs social" style="left:914px;top:29px;background:#2f7ab5"></div>
</footer>
</body>
</html>
```